Design a New Business Card for Our Company

We are looking for fresh, unique, and a modern business card that reflects our roots as digital marketing agency focused on SEM.

Industry/Entity Type

Marketing

Contact Information for Business Card

looking for very unique out of the box designs. clean and modern that compliments our logo

Requirements
Must have
• colors should match our logo
• Front should have name, address, email, and phone/fax of the person, phone/fax are the same number
• back should have our url

```html
<!DOCTYPE html>
<html lang="en">
<head>
<meta charset="utf-8">
<title>Brightpath Digital – Business Card</title>
<link href="https://fonts.googleapis.com/css2?family=Open+Sans:wght@400;600;700&display=swap" rel="stylesheet">
<style>
  :root {
    --brand-blue: #5b97d1;
    --brand-grey: #a9a9a9;
    --text-grey: #8c8c8c;
    --card-white: #ffffff;
    --stage: #ecebe8;
    --rule: #cfcfcf;
  }
  * { margin: 0; padding: 0; box-sizing: border-box; }
  html, body {
    width: 1200px; height: 675px; overflow: hidden;
    background: var(--stage);
    font-family: "Open Sans", Arial, sans-serif;
  }
  .card {
    position: absolute; top: 195px;
    width: 500px; height: 286px;
    background: var(--card-white);
    box-shadow: 0 2px 10px rgba(0,0,0,0.12);
    overflow: hidden;
  }
  .card-back { left: 70px; }
  .card-front { left: 630px; }

  /* Back */
  .back-brand {
    position: absolute; top: 104px; left: 0; width: 100%;
    display: flex; align-items: center; justify-content: center; gap: 12px;
  }
  .back-brand .brand-dot {
    width: 30px; height: 30px; border-radius: 50%; background: var(--brand-blue);
  }
  .back-brand .brand-name {
    font-size: 30px; font-weight: 600; color: var(--brand-grey); letter-spacing: -0.5px;
  }
  .back-url {
    position: absolute; left: 0; width: 100%; top: 226px; text-align: center;
    font-size: 14px; color: var(--text-grey);
  }
  .back-url strong { color: var(--brand-blue); font-weight: 400; }

  /* Front */
  .front-brand {
    position: absolute; left: 26px; top: 106px;
    display: flex; align-items: center; gap: 8px;
  }
  .front-brand .brand-dot {
    width: 18px; height: 18px; border-radius: 50%; background: var(--brand-blue);
  }
  .front-brand .brand-name {
    font-size: 21px; font-weight: 600; color: var(--brand-grey); letter-spacing: -0.3px;
  }
  .divider {
    position: absolute; left: 238px; top: 62px; width: 1px; height: 140px;
    background: var(--rule);
  }
  .contact {
    position: absolute; left: 252px; top: 58px; color: var(--text-grey);
    font-size: 12px; line-height: 1.35;
  }
  .person-name { font-size: 16px; font-weight: 700; color: var(--brand-blue); }
  .person-role { font-size: 12px; margin-bottom: 6px; }
  .company { font-size: 13px; color: var(--brand-blue); }
  .address { margin-bottom: 6px; }
  .contact-list { list-style: none; }
  .contact-list li { display: flex; align-items: center; gap: 7px; height: 17px; }
  .contact-list svg { width: 13px; height: 13px; flex: none; }
  .band-rule {
    position: absolute; left: 0; bottom: 44px; width: 100%; height: 3px;
    background: var(--brand-grey);
  }
  .band {
    position: absolute; left: 0; bottom: 0; width: 100%; height: 40px;
    background: var(--brand-blue);
  }
</style>
</head>
<body>

<section class="card card-back" aria-label="Card back">
  <div class="back-brand">
    <span class="brand-dot"></span>
    <span class="brand-name">Brightpath Digital</span>
  </div>
  <p class="back-url">www.<strong>brightpathdigital</strong>.com</p>
</section>

<section class="card card-front" aria-label="Card front">
  <div class="front-brand">
    <span class="brand-dot"></span>
    <span class="brand-name">Brightpath Digital</span>
  </div>
  <div class="divider"></div>
  <div class="contact">
    <p class="person-name">Owen Hartley</p>
    <p class="person-role">Owner</p>
    <p class="company">Brightpath Digital</p>
    <p class="address">N. 24 Cedar Lane, Suite 210,<br>Riverton, WA 50123</p>
    <ul class="contact-list">
      <li>
        <svg viewBox="0 0 14 14" aria-hidden="true"><circle cx="7" cy="7" r="7" fill="#5b97d1"/><path d="M4.5 3.5l1.6-.3.7 1.8-1 .7c.4 1 1.1 1.7 2.1 2.1l.7-1 1.8.7-.3 1.6C7.3 10 4 6.7 4.5 3.5z" fill="#fff"/></svg>
        555.010.204
      </li>
      <li>
        <svg viewBox="0 0 14 14" aria-hidden="true"><circle cx="7" cy="7" r="7" fill="#5b97d1"/><rect x="3.5" y="5.5" width="7" height="4" rx="0.6" fill="#fff"/><rect x="5" y="3.5" width="4" height="2" fill="#fff"/></svg>
        555.010.204
      </li>
      <li>
        <svg viewBox="0 0 14 14" aria-hidden="true"><circle cx="7" cy="7" r="7" fill="#5b97d1"/><rect x="3.5" y="4.5" width="7" height="5" fill="#fff"/><path d="M3.5 4.5L7 7.3l3.5-2.8" fill="none" stroke="#5b97d1" stroke-width="0.8"/></svg>
        info@brightpathdigital.com
      </li>
      <li>
        <svg viewBox="0 0 14 14" aria-hidden="true"><circle cx="7" cy="7" r="7" fill="#5b97d1"/><circle cx="7" cy="7" r="3.6" fill="none" stroke="#fff" stroke-width="0.9"/><path d="M3.4 7h7.2M7 3.4c-1.6 2-1.6 5.2 0 7.2M7 3.4c1.6 2 1.6 5.2 0 7.2" fill="none" stroke="#fff" stroke-width="0.7"/></svg>
        www.brightpathdigital.com
      </li>
    </ul>
  </div>
  <div class="band-rule"></div>
  <div class="band"></div>
</section>

</body>
</html>
```